Redesign of outdated "Automotive Automation Company"

We are looking to finally update our outdated website with some cutting edge graphics. We want our customers to know we value technology and are cutting edge as far as design. We provide automation solutions for the automotive industry which essentially means we program robots, and sell automation related products.

Current URL

http://lnk.qorvi.example/Tm4pzr
Updates

Project Deadline Extended
Reason: The client portal wasn't working, it's just finally been fixed by Pixel Harbor. I will go through and start reviewing designs.

We are trying to go with the same look and feel on our business cards, line cards, apparel, etc. so we are forming a brand. I have included the current draft of the line card. Please utilize our newest Logo VEL Standardized Logo.jpg http://img.plomtra.example/zuKe9rb.jpg?1 Also we are trying hard to sell the following software / hardware companies so we can put some emphasis on their product. Corvane Systems https://www.corvanesystems.example/ We make money on selling the software and then on the integration. I think you should tie in this animation. ยท Shop Line Muddle to Momentum https://media.vuntelo.example/clips/9b2e7f1d04c3a85e6f2d1b7c9a0e4f3d8c6b2a1e.jpg?image_play_button=true&image_play_button_color=7b796ae0&image_crop_resized=275x155 In this 2-minute video, discover how Trellan can help run your plant floor. We are Authorized Integrators / Resellers for Pembry Controls Hadrix Sensorik http://hadrix.example/en/usa/ Corvane Systems https://www.corvanesystems.example/ Unified Motion Works www.umwkq.example Brisk Beltway Corp www.briskbeltway.example Castmere Fabrication http://www.castmerefab.example/strategic_partners.aspx

Target Market(s)

Large automotive companies looking for automation or robotic programming. So Professional is key.

Industry/Entity Type

Automotive

Font styles to use
Other font styles liked:
• Possible Open Sans or Lato

Colors
0591cc
ceeaf6
fbd4d5
fbf289
fece3e

Requirements
Must have
• Professional Modern Design.

I want a homepage design, and a rough Sales Page... Where numerous products can be listed.
Nice to have
• Maybe an updated logo if possible.

```html
<!DOCTYPE html>
<html lang="en">
<head>
<meta charset="utf-8">
<title>VEL Engineering Solutions</title>
<link href="https://fonts.googleapis.com/css2?family=Jost:wght@300;400;500;700&family=Arimo:wght@400;700&display=swap" rel="stylesheet">
<style>
:root{
  --green:#6cbf2c;
  --red:#e8174f;
  --blue:#0591cc;
  --navy:#163a6b;
  --yellow:#fece3e;
  --gold:#f5d020;
  --ink:#333333;
  --grey:#e4e4e6;
  --dark:#2b2b2b;
  --page-bg:#f3f3f3;
}
*{margin:0;padding:0;box-sizing:border-box}
html,body{width:828px;height:1200px;overflow:hidden}
body{background:var(--page-bg);font-family:"Arimo",Arial,sans-serif;color:var(--ink);position:relative}
.top-strip{position:absolute;left:0;top:0;width:828px;height:4px;background:var(--green)}
.page{position:absolute;left:69px;top:4px;width:691px;height:1076px;background:#fff;box-shadow:0 0 3px rgba(0,0,0,.25)}
.brand{position:absolute;left:24px;top:14px;display:flex;align-items:center;gap:8px}
.brand-dot{width:44px;height:44px;border-radius:50%;background:var(--red)}
.brand-name{font-family:"Jost",sans-serif;font-weight:700;font-size:30px;color:var(--ink);letter-spacing:1px}
.call{position:absolute;right:15px;top:17px;display:flex;align-items:center;gap:6px;font-family:"Jost",sans-serif;font-size:16px;color:#444}
.call b{font-weight:400;color:var(--blue)}
.nav{position:absolute;left:339px;top:56px;width:352px;height:29px;background:var(--red);clip-path:polygon(14px 0,100% 0,100% 100%,0 100%)}
.nav ul{list-style:none;display:flex;justify-content:space-between;padding:0 10px 0 38px;height:100%;align-items:center}
.nav li{font-family:"Jost",sans-serif;font-weight:300;font-size:12.5px;color:#fff}

.hero{position:absolute;left:0;top:85px;width:691px;height:340px;overflow:hidden;
  background:
    radial-gradient(ellipse 260px 120px at 560px 40px,rgba(235,240,246,.55),rgba(235,240,246,0) 70%),
    radial-gradient(ellipse 300px 160px at 600px 300px,rgba(70,100,135,.55),rgba(70,100,135,0) 70%),
    linear-gradient(100deg,#6c7c8e 0%,#9aa8b6 30%,#5d7187 62%,#93a3b3 100%)}
.hero-art{position:absolute;left:0;top:0;width:400px;height:340px;
  background:
    radial-gradient(ellipse 55px 75px at 290px 60px,#f8f9fa 0%,#dfe2e6 55%,rgba(223,226,230,0) 100%),
    radial-gradient(ellipse 50px 40px at 225px 150px,rgba(170,25,75,.75),rgba(170,25,75,0) 100%),
    radial-gradient(ellipse 45px 60px at 130px 115px,rgba(150,20,65,.7),rgba(150,20,65,0) 100%),
    radial-gradient(ellipse 150px 130px at 200px 190px,#fbfbfc 0%,#e3e6ea 45%,rgba(200,205,212,0) 100%),
    radial-gradient(ellipse 170px 70px at 230px 320px,#eef0f2 0%,#c9ced4 50%,rgba(160,168,178,0) 100%),
    radial-gradient(ellipse 70px 150px at 40px 250px,rgba(40,45,55,.55),rgba(40,45,55,0) 100%)}
.hero-copy{position:absolute;left:360px;top:108px;width:320px}
.hero-title{font-family:"Jost",sans-serif;font-weight:700;font-size:33px;line-height:38px;color:#fff;letter-spacing:.5px}
.hero-title span{color:var(--red)}
.hero-text{margin-top:14px;font-size:10px;line-height:17px;color:#fff}

.intro{position:absolute;left:0;top:425px;width:691px;height:151px;background:var(--blue);text-align:center;color:#fff}
.intro::after{content:"";position:absolute;left:337px;bottom:-9px;border-left:9px solid transparent;border-right:9px solid transparent;border-top:9px solid var(--blue)}
.intro h1{font-weight:400;font-size:21px;margin-top:15px}
.intro h2{font-weight:400;font-size:14.5px;color:var(--gold);margin-top:6px;padding-bottom:7px;border-bottom:1px solid rgba(255,255,255,.25);width:470px;margin-left:auto;margin-right:auto}
.intro p{font-size:9.7px;line-height:20.5px;padding:6px 10px 0}

.feature-cards{position:absolute;left:15px;top:618px;width:661px;display:flex;justify-content:space-between}
.card{width:196px;height:129px;border:2px solid #9a9a9a;position:relative}
.card-team{background:
    radial-gradient(ellipse 30px 60px at 70px 75px,rgba(255,255,255,.9),rgba(255,255,255,0) 100%),
    radial-gradient(ellipse 90px 50px at 150px 40px,rgba(140,200,245,.7),rgba(140,200,245,0) 100%),
    linear-gradient(135deg,#2d5a8c 0%,#5f8fc2 50%,#a8cbe8 100%)}
.card-plan{background:
    radial-gradient(ellipse 80px 40px at 110px 45px,rgba(200,225,250,.55),rgba(200,225,250,0) 100%),
    radial-gradient(ellipse 15px 30px at 28px 85px,rgba(60,60,70,.6),rgba(60,60,70,0) 100%),
    linear-gradient(135deg,#1f4f95 0%,#3b74c0 50%,#6fa2dc 100%)}
.card-ideas{background:
    radial-gradient(ellipse 60px 45px at 60px 55px,rgba(205,150,125,.75),rgba(205,150,125,0) 100%),
    radial-gradient(ellipse 40px 50px at 170px 30px,rgba(220,170,145,.7),rgba(220,170,145,0) 100%),
    linear-gradient(160deg,#f4f5f7 0%,#d9dde2 55%,#aab5c2 100%)}
.card-label{position:absolute;left:2px;right:2px;bottom:2px;height:25px;background:var(--red);display:flex;align-items:center;justify-content:space-between;padding:0 8px 0 6px;font-family:"Jost",sans-serif;font-size:10.5px;color:#fff}

.overview{position:absolute;left:0;top:792px;width:691px;height:284px;overflow:hidden;
  background:
    radial-gradient(ellipse 160px 120px at 600px 230px,rgba(200,200,204,.55),rgba(200,200,204,0) 100%),
    radial-gradient(ellipse 140px 100px at 120px 260px,rgba(205,205,209,.5),rgba(205,205,209,0) 100%),
    var(--grey)}
.overview-title{text-align:center;font-weight:400;font-size:29px;color:var(--navy);margin-top:14px}
.overview-rule{width:236px;height:1px;background:var(--red);margin:17px auto 0}
.services{display:flex;justify-content:space-between;padding:27px 14px 0 14px}
.service{width:200px;text-align:center}
.service-icon{width:67px;height:67px;border-radius:50%;background:var(--yellow);border:3px solid #fff;box-shadow:0 0 0 1px var(--yellow);margin:0 auto;display:flex;align-items:center;justify-content:center}
.service h3{font-weight:400;font-size:13px;color:#333;margin-top:13px}
.service p{font-size:9.6px;line-height:15px;color:#444;margin-top:5px}

.footer{position:absolute;left:0;top:1080px;width:828px;height:120px;background:var(--dark);border-top:4px solid var(--red)}
.footer-address{position:absolute;left:79px;top:10px;font-size:9.5px;line-height:16.5px;color:#fff;font-style:normal}
.footer-brand{position:absolute;left:655px;top:24px;display:flex;align-items:center;gap:6px}
.footer-brand .brand-dot{width:34px;height:34px}
.footer-brand .brand-name{color:#fff;font-size:24px}
.footer-rule{position:absolute;left:69px;top:84px;width:691px;height:1px;background:#444}
.footer-nav{position:absolute;left:0;top:96px;width:828px;text-align:center;font-size:9px;color:#fff}
.footer-nav span{margin:0 12px;color:#fff}
</style>
</head>
<body>
<div class="top-strip"></div>
<div class="page">
  <div class="brand"><div class="brand-dot"></div><div class="brand-name">VEL</div></div>
  <div class="call">
    <svg width="17" height="17" viewBox="0 0 17 17"><rect width="17" height="17" rx="3" fill="#0591cc"/><path d="M5 3.5l2 .3.8 2.6-1.3 1a7 7 0 0 0 3 3l1-1.3 2.6.8.3 2c-.3.8-1.2 1.3-2 1.1A9 9 0 0 1 3.9 5.5c-.2-.8.3-1.7 1.1-2z" fill="#fff"/></svg>
    Call : <b>555-271-3408</b>
  </div>
  <nav class="nav"><ul><li>Home Page</li><li>Services</li><li>Contact</li><li>About</li></ul></nav>

  <section class="hero">
    <div class="hero-art" role="img" aria-label="White humanoid robot with crimson accents seated in a thinking pose"></div>
    <div class="hero-copy">
      <div class="hero-title">VEL <span>ENGINEERING</span><br>SOLUTIONS</div>
      <p class="hero-text">Lorem ipsum dolor sit amet, consectetur adipiscing elit, sed do eiusmod culpa qui officia &nbsp;id est laborum.</p>
    </div>
  </section>

  <section class="intro">
    <h1>Your Premier Automation Consulting &amp; Systems Integration choice!</h1>
    <h2>Helping your business optimize its Automation....</h2>
    <p>Lorem ipsum dolor sit amet, consectetur adipiscing elit, sed do eiusmod tempor incididunt ut labore et dolore magna aliqua. Ut enim ad minim veniam, quis nostrud exercitation ullamco laboris nisi ut aliquip ex ea commodo consequat. Duis aute irure dolor in reprehenderit in voluptate velit esse cillum dolore eu fugiat nulla pariatur. Excepteur sint occaecat cupidatat non proident, sunt in culpa qui officia deserunt mollit anim id est laborum.</p>
  </section>

  <div class="feature-cards">
    <div class="card card-team" role="img" aria-label="Businessman touching a glowing digital chart display">
      <div class="card-label">Get to know our Team approach<svg width="17" height="17" viewBox="0 0 17 17"><circle cx="8.5" cy="8.5" r="7.5" fill="none" stroke="#fff" stroke-width="1.6"/><path d="M4.5 8.5h7M8.5 5.3l3.2 3.2-3.2 3.2" fill="none" stroke="#fff" stroke-width="1.8"/></svg></div>
    </div>
    <div class="card card-plan" role="img" aria-label="Man facing a blue board of business strategy sketches">
      <div class="card-label">This way to Automation success<svg width="17" height="17" viewBox="0 0 17 17"><circle cx="8.5" cy="8.5" r="7.5" fill="none" stroke="#fff" stroke-width="1.6"/><path d="M4.5 8.5h7M8.5 5.3l3.2 3.2-3.2 3.2" fill="none" stroke="#fff" stroke-width="1.8"/></svg></div>
    </div>
    <div class="card card-ideas" role="img" aria-label="Hands reviewing documents with a pen">
      <div class="card-label">Bring great ideas to your business<svg width="17" height="17" viewBox="0 0 17 17"><circle cx="8.5" cy="8.5" r="7.5" fill="none" stroke="#fff" stroke-width="1.6"/><path d="M4.5 8.5h7M8.5 5.3l3.2 3.2-3.2 3.2" fill="none" stroke="#fff" stroke-width="1.8"/></svg></div>
    </div>
  </div>

  <section class="overview" role="img" aria-label="Faint robotic machinery backdrop behind the overview">
    <h2 class="overview-title">OVERVIEW</h2>
    <div class="overview-rule"></div>
    <div class="services">
      <div class="service">
        <div class="service-icon"><svg width="32" height="32" viewBox="0 0 32 32"><path d="M6 6l20 20M26 6L6 26" stroke="#111" stroke-width="4" stroke-linecap="round"/></svg></div>
        <h3>DESIGN ENGINEERING</h3>
        <p>Provide electro-mechanical designs for machine sizing calculations for motion control and fluid power applications.</p>
      </div>
      <div class="service">
        <div class="service-icon"><svg width="34" height="34" viewBox="0 0 34 34"><path d="M19 4L9 19h7l-2 11 11-16h-7z" fill="#111"/><path d="M3 17h3M28 17h3M7 7l2 2M25 25l2 2M27 7l-2 2M7 27l2-2" stroke="#111" stroke-width="2"/></svg></div>
        <h3>ELECTRICAL ENGINEERING</h3>
        <p>Provide electro-mechanical designs for machine sizing calculations for motion control and fluid power applications.</p>
      </div>
      <div class="service">
        <div class="service-icon"><svg width="34" height="34" viewBox="0 0 34 34"><circle cx="13" cy="13" r="8" fill="none" stroke="#111" stroke-width="4" stroke-dasharray="3 2.3"/><circle cx="13" cy="13" r="3" fill="#111"/><circle cx="24" cy="24" r="6" fill="none" stroke="#111" stroke-width="3.5" stroke-dasharray="2.6 2"/><circle cx="24" cy="24" r="2" fill="#111"/></svg></div>
        <h3>APPLICATIONS ENGINEERING</h3>
        <p>Provide electro-mechanical designs for machine sizing calculations for motion control and fluid power applications.</p>
      </div>
    </div>
  </section>
</div>

<footer class="footer">
  <address class="footer-address">www.VelEngSolutions.example<br>472 W. Larkfield Road<br>PO Box 318<br>Brantford, MI 49017</address>
  <div class="footer-brand"><div class="brand-dot"></div><div class="brand-name">VEL</div></div>
  <div class="footer-rule"></div>
  <div class="footer-nav">Home Page<span>|</span>Services<span>|</span>Contact<span>|</span>About</div>
</footer>
</body>
</html>
```